UX Design for Analytics Web Application

http://velqoranthe.com/
We are tech & consulting company with analytics products (web applications), located at Rio de Janeiro, Brazil.

We are searching a partner do develop UX for our products, i.e, aesthetics, usability, HTML/CSS.

Currently we have a product suite and the goal is to make a pilot re-design project with one of our products.

The product of interest is interactive webapp that aims at data analysis, significantly different from blogs, e-commerce or landing pages.

We do have a software development team but we lack an UX & HTML expert. Currently we use Bootstrap templates but the results are insatisfatory.

So, the project scope is, to develop the arts (UX, aesthetics, etc) along with the code/mockup (HTML/CSS) for one of our product (3 pages).

This is a pilot project and there's potential to rehire for our other products. Code quality is of importance.

More details and specification can be found in attached files.

Target Market(s)

Executives, managers & consultants

Industry/Entity Type

It Company

Coding

Coded - Design and coding required

Number of Pages Required

3 page

Font styles to use
Sans Serif

Requirements
Must have
• (see attached files, prefer the pptx version))
• -Responsive
Nice to have
• (see attached files, prefer the pptx version)
Should not have
• -Avoid Green, Red and Yellow colors. They have a meaning of good, bad and average in our products.

```html
<!DOCTYPE html>
<html lang="en">
<head>
<meta charset="utf-8">
<title>Velqoranthe — Process Dashboard</title>
<link href="https://fonts.googleapis.com/css2?family=Open+Sans:wght@400;600;700;800&display=swap" rel="stylesheet">
<style>
:root{
  --navy:#3f5068;
  --navy-deep:#1c2333;
  --ink:#333333;
  --card-dark:#3a3a3a;
  --step-done:#3b9b12;
  --step-active:#4fb8f0;
  --step-idle:#a8a8a8;
  --card-idle:#d9d9d9;
  --muted:#5c5c5c;
  --rule:#dcdcdc;
  --footer:#e5e5e5;
  --white:#ffffff;
}
*{box-sizing:border-box;margin:0;padding:0}
html,body{width:1200px;height:952px;overflow:hidden;background:var(--white);font-family:"Open Sans",Arial,sans-serif;color:var(--ink)}
.app{position:relative;width:1200px;height:952px}

/* header */
.topbar{position:absolute;left:0;top:0;width:1200px;height:128px;border-bottom:2px solid var(--rule)}
.menu-toggle{position:absolute;left:24px;top:52px;width:28px;height:24px;display:flex;flex-direction:column;justify-content:space-between}
.menu-toggle span{display:block;height:5px;background:var(--ink);border-radius:1px}
.brand{position:absolute;left:132px;top:44px;display:flex;align-items:center;gap:10px}
.brand-dot{width:22px;height:22px;border-radius:50%;background:var(--ink)}
.brand-name{font-size:32px;font-weight:700;color:var(--ink);letter-spacing:-0.5px}
.actions{position:absolute;right:133px;top:44px;display:flex;gap:32px}
.action{position:relative;width:40px;height:40px;border-radius:50%;background:var(--ink);display:flex;align-items:center;justify-content:center}
.badge{position:absolute;left:-9px;top:-6px;width:20px;height:20px;border-radius:50%;background:var(--step-active);color:var(--white);font-size:9px;display:flex;align-items:center;justify-content:center}

/* side navigation */
.sidenav{position:absolute;left:132px;top:146px;width:298px}
.nav-head{height:48px;background:var(--navy);color:var(--white);font-size:16px;display:flex;align-items:center;padding-left:14px;margin-bottom:8px}
.nav-head .caret{width:0;height:0;border-left:4px solid transparent;border-right:4px solid transparent;margin-right:10px}
.caret.down{border-top:5px solid var(--white)}
.caret.up{border-bottom:5px solid var(--white)}
.nav-head.open{margin-bottom:0}
.subnav{background:var(--navy-deep);margin-bottom:8px}
.subnav-item{height:40px;display:flex;align-items:center;padding-left:30px;font-size:13px;color:#9aa3b5;border-bottom:1px solid #2c3447}
.subnav-item:last-child{border-bottom:none}
.subnav-item.current{color:var(--white)}
.subnav-item svg{margin-right:16px}
.nav-button{height:48px;background:var(--navy);color:var(--white);font-size:16px;display:flex;align-items:center;justify-content:center;gap:6px;margin-bottom:8px}

/* steps */
.steps{position:absolute;left:451px;top:146px;width:298px}
.step{position:relative;height:80px;display:flex;background:var(--card-idle);margin-bottom:24px}
.step-icon{position:relative;width:64px;height:80px;background:var(--step-idle);display:flex;align-items:center;justify-content:center}
.step-icon::after{content:"";position:absolute;left:24px;bottom:-10px;border-left:8px solid transparent;border-right:8px solid transparent;border-top:10px solid var(--step-idle)}
.step-body{padding:14px 14px 0 15px}
.step-title{font-size:13px;color:#4a4a4a;margin-bottom:5px}
.step-text{font-size:8.6px;line-height:13px;color:var(--muted)}
.step.done{background:var(--card-dark)}
.step.done .step-icon{background:var(--step-done)}
.step.done .step-icon::after{border-top-color:var(--step-done)}
.step.done .step-title{color:var(--white)}
.step.done .step-text{color:#a9a9a9}
.step.active{background:var(--navy)}
.step.active .step-icon{background:var(--step-active)}
.step.active .step-icon::after{border-top-color:var(--step-active)}
.step.active .step-title{color:var(--white)}
.step.active .step-text{color:#b9c3d3}
.flag{position:absolute;right:0;top:0;width:13px;height:13px;display:flex;align-items:center;justify-content:center}
.done .flag{background:#2f7d0e}
.active .flag{background:#2f95cc}

/* stat panel */
.stat{position:absolute;left:769px;top:146px;width:298px;height:704px;background:var(--navy);color:var(--white)}
.stat-value{position:absolute;left:28px;top:-6px;font-size:112px;font-weight:800;letter-spacing:-4px;line-height:1.2}
.stat-label{position:absolute;left:34px;top:106px;font-size:24px}

/* footer */
.footer{position:absolute;left:0;top:896px;width:1200px;height:56px;background:var(--footer);font-size:11px;color:var(--ink);text-align:center;padding-top:17px}
</style>
</head>
<body>
<div class="app">
  <header class="topbar">
    <div class="menu-toggle"><span></span><span></span><span></span></div>
    <div class="brand"><span class="brand-dot"></span><span class="brand-name">Velqoranthe</span></div>
    <div class="actions">
      <div class="action"><span class="badge">0</span>
        <svg width="16" height="16" viewBox="0 0 16 16"><path d="M8 1a1 1 0 0 1 1 1v.6A4.5 4.5 0 0 1 12.5 7v3.5l1.5 1.8H2l1.5-1.8V7A4.5 4.5 0 0 1 7 2.6V2a1 1 0 0 1 1-1zM6.3 13.3h3.4a1.7 1.7 0 0 1-3.4 0z" fill="#fff"/></svg></div>
      <div class="action"><svg width="14" height="16" viewBox="0 0 14 16"><circle cx="7" cy="4.5" r="3.5" fill="#fff"/><path d="M0 15c0-4 3-6 7-6s7 2 7 6z" fill="#fff"/></svg></div>
      <div class="action"><svg width="16" height="16" viewBox="0 0 16 16"><path d="M7 0h2l.4 2.2 1.5.6 1.9-1.3 1.4 1.4-1.3 1.9.6 1.5L16 7v2l-2.2.4-.6 1.5 1.3 1.9-1.4 1.4-1.9-1.3-1.5.6L9 16H7l-.4-2.2-1.5-.6-1.9 1.3-1.4-1.4 1.3-1.9-.6-1.5L0 9V7l2.2-.4.6-1.5-1.3-1.9 1.4-1.4 1.9 1.3 1.5-.6z" fill="#fff"/><circle cx="8" cy="8" r="2.6" fill="#333"/></svg></div>
    </div>
  </header>

  <nav class="sidenav">
    <div class="nav-head"><span class="caret down"></span>Process 1</div>
    <div class="nav-head open"><span class="caret up"></span>Process 2</div>
    <div class="subnav">
      <div class="subnav-item current"><svg width="11" height="11" viewBox="0 0 16 16"><path d="M7 0h2l.4 2.2 1.5.6 1.9-1.3 1.4 1.4-1.3 1.9.6 1.5L16 7v2l-2.2.4-.6 1.5 1.3 1.9-1.4 1.4-1.9-1.3-1.5.6L9 16H7l-.4-2.2-1.5-.6-1.9 1.3-1.4-1.4 1.3-1.9-.6-1.5L0 9V7l2.2-.4.6-1.5-1.3-1.9 1.4-1.4 1.9 1.3 1.5-.6z" fill="#fff"/><circle cx="8" cy="8" r="2.6" fill="#1c2333"/></svg>Setup</div>
      <div class="subnav-item"><svg width="14" height="11" viewBox="0 0 14 11" fill="none" stroke="#9aa3b5"><path d="M.5 0v10.5H14"/><path d="M3 10V6M5 10V3M7 10V5M9 10V2M11 10V4"/></svg>Analysis</div>
      <div class="subnav-item"><svg width="12" height="12" viewBox="0 0 12 12" fill="none" stroke="#9aa3b5"><path d="M.5 2.5h3l2 2v4h-5z"/><path d="M5.5 4.5h3l3 3v4h-6z"/><path d="M3.5 2.5V.5h3l2 2v2"/></svg>Comparision &amp; Selection</div>
    </div>
    <div class="nav-head"><span class="caret down"></span>Process 3</div>
    <div class="nav-button"><svg width="12" height="12" viewBox="0 0 12 12"><circle cx="6" cy="6" r="6" fill="#fff"/><path d="M6 3v6M3 6h6" stroke="#3f5068" stroke-width="2"/></svg>New Process</div>
    <div class="nav-button"><svg width="13" height="11" viewBox="0 0 13 11"><path d="M6.5 0L13 5.5h-2V11H8V7.5H5V11H2V5.5H0z" fill="#fff"/></svg>Overview</div>
  </nav>

  <section class="steps">
    <div class="step done">
      <div class="step-icon"><svg width="30" height="30" viewBox="0 0 16 16"><path d="M7 0h2l.4 2.2 1.5.6 1.9-1.3 1.4 1.4-1.3 1.9.6 1.5L16 7v2l-2.2.4-.6 1.5 1.3 1.9-1.4 1.4-1.9-1.3-1.5.6L9 16H7l-.4-2.2-1.5-.6-1.9 1.3-1.4-1.4 1.3-1.9-.6-1.5L0 9V7l2.2-.4.6-1.5-1.3-1.9 1.4-1.4 1.9 1.3 1.5-.6z" fill="#fff"/><circle cx="8" cy="8" r="2.6" fill="#3b9b12"/></svg><span class="flag"><svg width="7" height="6" viewBox="0 0 7 6"><path d="M.5 3l2 2L6.5.5" stroke="#fff" fill="none" stroke-width="1.4"/></svg></span></div>
      <div class="step-body"><div class="step-title">Setup</div><div class="step-text">Maecenas mi eros, auctor at ultrices in, egestas tempus diam. Proin fermentum neque.</div></div>
    </div>
    <div class="step active">
      <div class="step-icon"><svg width="36" height="28" viewBox="0 0 36 28" fill="none" stroke="#fff" stroke-width="2"><path d="M1 0v27h35"/><path d="M8 25v-8M14 25V12M20 25v-6M26 25V8" stroke-width="4"/></svg><span class="flag"><svg width="7" height="7" viewBox="0 0 7 7" fill="none" stroke="#fff" stroke-width="1.2"><path d="M6 3.5A2.5 2.5 0 1 1 4.7 1.3M4.5.3l.5 1.2-1.2.4"/></svg></span></div>
      <div class="step-body"><div class="step-title">Analysis</div><div class="step-text">Maecenas mi eros, auctor at ultrices in, egestas tempus diam. Proin fermentum neque.</div></div>
    </div>
    <div class="step">
      <div class="step-icon"><svg width="30" height="30" viewBox="0 0 30 30" fill="none" stroke="#fff" stroke-width="2"><path d="M2 8h8l5 5v11H2z"/><path d="M13 13h8l7 7v9H13z"/><path d="M9 8V2h8l5 5v6"/></svg></div>
      <div class="step-body"><div class="step-title">Comparison &amp; Selection</div><div class="step-text">Maecenas mi eros, auctor at ultrices in, egestas tempus diam. Proin fermentum neque.</div></div>
    </div>
    <div class="step">
      <div class="step-icon"><svg width="34" height="30" viewBox="0 0 34 30" fill="#fff"><circle cx="7" cy="6" r="4"/><circle cx="27" cy="6" r="4"/><circle cx="17" cy="10" r="6"/><path d="M0 18c0-4 3-5 7-5s5 1 5 2v3zM34 18c0-4-3-5-7-5s-5 1-5 2v3zM7 30c0-8 4-11 10-11s10 3 10 11z"/></svg></div>
      <div class="step-body"><div class="step-title">Executive Negotiation</div><div class="step-text">Maecenas mi eros, auctor at ultrices in, egestas tempus diam. Proin fermentum neque.</div></div>
    </div>
    <div class="step">
      <div class="step-icon"><svg width="24" height="30" viewBox="0 0 24 30" fill="none" stroke="#fff" stroke-width="1.6"><path d="M1 1h22v28H1z"/><path d="M9 29v-5h6v5" /><g stroke-width="2"><path d="M5 5h2M11 5h2M17 5h2M5 10h2M11 10h2M17 10h2M5 15h2M11 15h2M17 15h2M5 20h2M11 20h2M17 20h2"/></g></svg></div>
      <div class="step-body"><div class="step-title">Per Entity Negotiation</div><div class="step-text">Maecenas mi eros, auctor at ultrices in, egestas tempus diam. Proin fermentum neque.</div></div>
    </div>
    <div class="step">
      <div class="step-icon"><svg width="28" height="30" viewBox="0 0 28 30" fill="none" stroke="#fff" stroke-width="2"><rect x="1" y="1" width="26" height="28" rx="2"/><path d="M5 5h18v6H5z" fill="#fff"/><g fill="#fff" stroke="none"><circle cx="6" cy="16" r="1.8"/><circle cx="11.3" cy="16" r="1.8"/><circle cx="16.6" cy="16" r="1.8"/><circle cx="22" cy="16" r="1.8"/><circle cx="6" cy="20.5" r="1.8"/><circle cx="11.3" cy="20.5" r="1.8"/><circle cx="16.6" cy="20.5" r="1.8"/><circle cx="22" cy="20.5" r="1.8"/><circle cx="6" cy="25" r="1.8"/><circle cx="11.3" cy="25" r="1.8"/><circle cx="16.6" cy="25" r="1.8"/><circle cx="22" cy="25" r="1.8"/></g></svg></div>
      <div class="step-body"><div class="step-title">Balance Review</div><div class="step-text">Maecenas mi eros, auctor at ultrices in, egestas tempus diam. Proin fermentum neque.</div></div>
    </div>
    <div class="step">
      <div class="step-icon"><svg width="36" height="28" viewBox="0 0 36 28" fill="none" stroke="#fff" stroke-width="2.4"><path d="M1 0v27h35"/><path d="M6 21l8-8 5 5 11-11"/><path d="M24 6h7v7" /></svg></div>
      <div class="step-body"><div class="step-title">Export Results</div><div class="step-text">Maecenas mi eros, auctor at ultrices in, egestas tempus diam. Proin fermentum neque.</div></div>
    </div>
  </section>

  <aside class="stat">
    <div class="stat-value">236</div>
    <div class="stat-label">Analysis Saved</div>
  </aside>

  <footer class="footer">Copyright &nbsp;©&nbsp; 2017 &nbsp;Company name.&nbsp; All rights reserved.</footer>
</div>
</body>
</html>
```